Design eines Hausetiketts für traditionelles Weingut
Zielgruppe
Wir das Familienweingut Brandauer in Gimbsheim/Rheinhessen sind ein traditionelles Weingut das seine Reben selbst kultiviert und die Weine auch selbst ausbaut. Wir haben jeden Schritt in der Weinherstellung selbst in der Hand und vermarkten den Wein dann an unsere Privatkunden. Unsere Kundenstruktur sieht folgendermaßen aus: Wir haben 100% Privatkunden die unseren Wein konsumieren. Da jetzt die nächste Generation in den Weinbaubetrieb einsteigt und auch Ideen hat möchten wir ein Hausetikett einführen. Im Moment haben wir noch sehr viele unterschiedliche Etiketten und kein Hausetikett. Da die Verlagsetiketten immer seltener zu unseren Vorstellungen passen, möchten wir hier auf diesem Wege ein Hausetikett anfertigen lassen. Generell möchten wir unseren Außenauftritt komplett modernisieren. Sie können sich über die Vielfalt in unserem Betrieb unter www.weingut-brandauer-beispiel.de einen Überblick verschaffen. Langfristig gesehen wollen wir aber unsere Weinkarte verkleinern.
Aufgabenstellung
Wir haben uns vor ca. 1,5 Jahren hier auf dieser Website bereits ein Logo designen lassen. Es wäre schön wenn man das Logo bei den Entwürfen für die Etiketten berücksichtigen würde. Das wäre aber KEIN MUSS. Auch wäre es gut wenn man das ,,Wein' bei unserem Namen weglassen könnte.
Das Etikett sollte aus Vorder-und Rückenetikett bestehen und edel wirken. Vorne sollte die Rebsorte und die Geschmacksangabe stehen. Der Rest sollte auf das Rückenetikett.
Das Vorderetikett sollte ein richtiger Eyecatcher sein und im Supermarkt z.B. aus vielen anderen herausstechen. Das wäre ganz wichtig.
Man kann bei den Farben unterscheiden in 3 Konzepte.
Literwein als einsteiger Wein
Dann die Gutsweine und zum Schluss die Lagenweine. Alles Farblich oder im design etwas abgesetzt.

```html
<!DOCTYPE html>
<html lang="de">
<head>
<meta charset="utf-8">
<title>Weißburgunder trocken – Hausetikett Brandauer</title>
<link rel="stylesheet" href="https://fonts.googleapis.com/css2?family=Cormorant+Garamond:wght@500;700&family=Lato:wght@400&display=swap">
<style>
  :root {
    --page: #ffffff;
    --paper: #f2f0ea;
    --paper-edge: #e4e1d8;
    --green: #1d5a4c;
    --teal: #1f5e57;
    --gold: #c4a24a;
    --gold-line: #cdb36a;
    --white: #ffffff;
  }
  html, body {
    margin: 0;
    width: 1200px;
    height: 1200px;
    overflow: hidden;
    background: var(--page);
  }
  .canvas {
    position: relative;
    width: 1200px;
    height: 1200px;
  }
  .front-label {
    position: absolute;
    left: 175px;
    top: 155px;
    width: 850px;
    height: 890px;
    background:
      repeating-linear-gradient(90deg, rgba(0,0,0,0.012) 0 2px, transparent 2px 5px),
      linear-gradient(180deg, var(--paper) 0%, #efede6 100%);
    box-shadow: 0 0 0 1px var(--paper-edge);
  }
  .label-frame {
    position: absolute;
    left: 70px;
    top: 140px;
    width: 710px;
    height: 600px;
    border: 2px dashed var(--gold-line);
    box-sizing: border-box;
  }
  .variety {
    position: absolute;
    left: 0;
    right: 0;
    top: 200px;
    margin: 0;
    text-align: center;
    font-family: "Cormorant Garamond", serif;
    font-weight: 700;
    font-size: 72px;
    color: var(--green);
    letter-spacing: 0.5px;
  }
  .taste {
    position: absolute;
    left: 0;
    right: 0;
    top: 330px;
    margin: 0;
    text-align: center;
    font-family: "Cormorant Garamond", serif;
    font-weight: 700;
    font-size: 52px;
    color: var(--green);
  }
  .vintage {
    position: absolute;
    left: 606px;
    top: 462px;
    width: 120px;
    height: 120px;
    border-radius: 50%;
    background: var(--teal);
    color: var(--white);
    display: flex;
    align-items: center;
    justify-content: center;
    font-family: "Lato", sans-serif;
    font-size: 31px;
    letter-spacing: 1px;
  }
  .brand-dot {
    position: absolute;
    left: 410px;
    top: 600px;
    width: 28px;
    height: 28px;
    border-radius: 50%;
    background: var(--gold);
  }
  .brand-name {
    position: absolute;
    left: 0;
    right: 0;
    top: 690px;
    margin: 0;
    text-align: center;
    font-family: "Cormorant Garamond", serif;
    font-weight: 500;
    font-size: 96px;
    line-height: 1;
    color: var(--gold);
    letter-spacing: -1px;
  }
</style>
</head>
<body>
  <main class="canvas">
    <section class="front-label">
      <div class="label-frame"></div>
      <h1 class="variety">Weißburgunder</h1>
      <p class="taste">trocken</p>
      <div class="vintage">2020</div>
      <span class="brand-dot"></span>
      <p class="brand-name">BRANDAUER</p>
    </section>
  </main>
</body>
</html>
```